Landing Page  Erste Hilfe und Rettung für Veranstaltung
Landing Page Erste Hilfe und Rettung für Veranstaltung
Zielgruppe
Professionelle Erste Hilfe und Rettung für Ihre Veranstaltung
Aufgabenstellung
Design soll zum Flimmora Account passen.. wichtig ist die Gelde-Farbe vom RTW! Farbe = RAL 1016

```html
<!DOCTYPE html>
<html lang="de">
<head>
<meta charset="utf-8">
<title>Silberpfeil Sanitätsdienst – Sanitätsdienst für Veranstaltungen</title>
<link rel="stylesheet" href="https://fonts.googleapis.com/css2?family=Raleway:wght@400;500;600;700;800;900&display=swap">
<style>
  :root{
    --navy:#1b3a8c;
    --navy-deep:#17327d;
    --yellow:#e6f51c;
    --ice:#e6f3fd;
    --ink:#1b3a8c;
    --white:#ffffff;
  }
  *{box-sizing:border-box;margin:0;padding:0}
  html,body{width:1200px;height:4280px;overflow:hidden}
  body{position:relative;background:var(--white);font-family:"Raleway",sans-serif;color:var(--ink)}
  .abs{position:absolute}
  .center{text-align:center;left:0;width:1200px}

  .top-line{top:0;left:0;width:1200px;height:7px;background:var(--yellow)}

  /* hero */
  .hero-photo{top:0;left:416px;width:784px;height:628px;border-bottom-left-radius:140px;
    background:linear-gradient(180deg,#3d7fd0 0%,#7fb3e6 35%,#b9d35b 62%,#6f8f3a 80%,#a69a7a 100%);
    box-shadow:0 14px 22px rgba(27,58,140,.12)}
  .nav{top:38px;left:37px;width:1126px;height:58px}
  .nav svg{position:absolute;inset:0}
  .brand{position:absolute;left:20px;top:16px;display:flex;align-items:center;gap:8px;color:var(--white);font-weight:700;font-size:11px;line-height:12px}
  .brand i{width:20px;height:20px;border-radius:50%;background:var(--yellow);display:block}
  .nav ul{position:absolute;left:400px;top:21px;display:flex;list-style:none;gap:0}
  .nav li{color:var(--white);font-size:11.5px;font-weight:600;margin-right:35px}
  .hero-badge{top:274px;left:387px;width:138px;height:138px;border-radius:50%;background:var(--yellow)}
  .welcome{top:191px;left:100px;height:55px;padding:0 18px;background:var(--navy);border-radius:3px;
    font-weight:900;font-size:27px;line-height:55px;color:var(--white);letter-spacing:.2px}
  .welcome span{color:var(--yellow)}
  .hero-sub{top:258px;left:118px;font-weight:600;font-size:20px}
  .hero-text{top:306px;left:118px;width:265px;font-size:14.5px;line-height:18.8px}
  .down{top:573px;left:120px;width:56px;height:56px;border-radius:50%;background:var(--yellow)}

  /* services */
  .services-bg{top:665px;left:0;width:1200px;height:1355px;background:linear-gradient(180deg,#fff 0%,var(--ice) 22%,#e9f4fd 100%)}
  .eyebrow{font-size:17px;font-weight:400}
  .h2{font-size:28px;font-weight:700;line-height:32px}
  .rule{width:100px;height:4px;left:550px}
  .rule.y{background:var(--yellow)}
  .rule.b{background:var(--navy)}
  .lead{font-size:14.5px;line-height:18.5px;text-align:center}
  .card{top:1079px;width:236px;height:256px;background:var(--white);border-radius:6px;
    box-shadow:0 4px 14px rgba(27,58,140,.12);text-align:center}
  .card .ico{position:absolute;left:76px;top:-44px;width:84px;height:84px;border-radius:50%;background:var(--navy)}
  .card .ico svg{position:absolute;left:22px;top:22px}
  .card h3{position:absolute;top:65px;left:0;width:100%;font-size:19px;font-weight:700}
  .card p{position:absolute;top:104px;left:30px;width:176px;font-size:11.5px;line-height:18.6px}

  .cols{top:1620px;left:331px;width:538px;display:flex;gap:36px;font-size:14.3px;line-height:18.6px}
  .cols p{width:251px;text-align:justify;hyphens:auto}
  .slide{top:1895px;left:120px;width:962px;height:505px;border-radius:12px;
    background:linear-gradient(120deg,#2a3f6e 0%,#5b6f8f 35%,#9aa2a8 60%,#6c7a8f 100%)}
  .job{top:1819px;left:872px;width:144px;height:144px;border-radius:50%;background:var(--navy);color:var(--white);
    font-weight:900;text-align:center;padding-top:38px;font-size:30px;line-height:30px;transform:rotate(12deg)}
  .job small{display:block;font-size:22px}
  .job b{color:var(--yellow)}
  .arrow{width:50px;height:40px}
  .dots{top:2422px;left:551px;display:flex;gap:6px}
  .dots i{width:15px;height:15px;border-radius:50%;background:var(--navy);display:block}
  .dots i.on{background:var(--yellow)}

  /* partners */
  .partner{width:190px;text-align:center;font-weight:700;font-size:17px;color:#111}

  /* staff */
  .staff-bg{top:2992px;left:0;width:1200px;height:811px;background:var(--navy);border-bottom-left-radius:32px;border-bottom-right-radius:32px}
  .staff-photo{top:3083px;left:116px;width:487px;height:607px;border-radius:20px;
    background:linear-gradient(180deg,#3b3b3b 0%,#8fb4d9 18%,#bcd3e6 45%,#2a3a66 70%,#26305a 100%)}
  .staff-title{top:3100px;left:661px;color:var(--white);font-size:28px;font-weight:700;line-height:32px}
  .staff-text{top:3193px;left:661px;width:404px;color:var(--white);font-size:14.3px;line-height:18.7px}
  .acc{left:661px;width:421px;background:var(--white);border:2px solid var(--yellow);border-radius:5px;padding:12px 18px;font-size:14px;font-weight:500}
  .acc .sign{position:absolute;right:14px;top:10px;font-size:26px;font-weight:800;line-height:22px}
  .acc .bar{width:62px;height:2px;background:var(--yellow);margin:4px 0 10px}
  .acc p{font-size:11.5px;line-height:18px;width:360px}

  /* jobs */
  .jobs{top:3751px;left:236px;width:726px;height:399px;background:var(--white);border-radius:6px;box-shadow:0 4px 18px rgba(27,58,140,.14);text-align:center}
  .btn{position:absolute;left:287px;top:308px;width:154px;height:41px;border-radius:21px;background:var(--yellow);
    box-shadow:0 4px 10px rgba(230,245,28,.5);font-size:11px;font-weight:700;line-height:41px}
</style>
</head>
<body>
<div class="abs top-line"></div>

<header>
  <div class="abs hero-photo" role="img" aria-label="Gelber Rettungswagen mit blauen Streifen auf einer Wiese, darüber ein gelber Rettungshubschrauber"></div>
  <nav class="abs nav">
    <svg width="1126" height="58" viewBox="0 0 1126 58"><path d="M6 0H1126L1090 58H6Q0 58 0 52V6Q0 0 6 0Z" fill="#1b3a8c"/></svg>
    <div class="brand"><i></i><span>Silberpfeil<br>Sanitätsdienst</span></div>
    <ul><li>Home</li><li>Leistungen</li><li>Einblicke</li><li>Referenzen</li><li>Personal</li><li>Ausrüstung</li><li>Buchung</li><li>FAQ</li></ul>
  </nav>
  <div class="abs hero-badge"></div>
  <h1 class="abs welcome">HERZLICH <span>WILLKOMMEN</span></h1>
  <p class="abs hero-sub">bei Silberpfeil Sanitätsdienst</p>
  <p class="abs hero-text">Wir freuen uns, dich als Besucher begrüßen zu dürfen. Als privater Anbieter für medizinische Absicherung aus Berlin haben wir uns seit über 15 Jahren auf Festivals, Clubs und Veranstaltungen spezialisiert. Unser Hauptaugenmerk liegt darauf, dass jede Veranstaltung optimal abgesichert ist. Dafür sorgen unsere stets gut ausgebildeten und sorgfältig ausgewählten Rettungsanitäter.</p>
  <div class="abs down"><svg width="56" height="56" viewBox="0 0 56 56"><path d="M28 15V38M18 29L28 40L38 29" stroke="#1b3a8c" stroke-width="6" fill="none" stroke-linecap="round" stroke-linejoin="round"/></svg></div>
</header>

<section>
  <div class="abs services-bg"></div>
  <p class="abs center eyebrow" style="top:746px">Unsere Leistungen</p>
  <h2 class="abs center h2" style="top:784px">Sanitätsdienst für<br>Veranstaltungen und Events</h2>
  <div class="abs rule y" style="top:871px"></div>
  <p class="abs lead" style="top:913px;left:316px;width:568px">Wenn du medizinisches Personal für die genannten Bereiche benötigst, freuen wir uns, wenn du direkt Kontakt mit uns aufnimmst. Unser Team bei Silberpfeil steht bereit, um deine Anforderungen zu besprechen und die passenden Fachkräfte für deine Veranstaltung oder dein Projekt bereitzustellen.</p>

  <div class="abs card" style="left:113px"><div class="ico"><svg width="40" height="40" viewBox="0 0 40 40"><path d="M14 30L26 12" stroke="#e6f51c" stroke-width="5" stroke-linecap="round"/><circle cx="28" cy="10" r="6" fill="#e6f51c"/></svg></div><h3>KONZERTE</h3><p>Lorem ipsum dolor sit amet, consetetur sadipscing elitr, sed diam nonumy eirmod tempor invidunt ut labore et dolore magna aliquyam erat, sed diam voluptua</p></div>
  <div class="abs card" style="left:359px"><div class="ico"><svg width="40" height="40" viewBox="0 0 40 40"><circle cx="20" cy="20" r="16" fill="#e6f51c"/><circle cx="20" cy="20" r="5" fill="#1b3a8c"/></svg></div><h3>SPORTEVENTS</h3><p>Lorem ipsum dolor sit amet, consetetur sadipscing elitr, sed diam nonumy eirmod tempor invidunt ut labore et dolore magna aliquyam erat, sed diam voluptua</p></div>
  <div class="abs card" style="left:605px"><div class="ico"><svg width="40" height="40" viewBox="0 0 40 40"><circle cx="13" cy="16" r="8" fill="#e6f51c"/><circle cx="27" cy="16" r="8" fill="#e6f51c"/><circle cx="20" cy="10" r="8" fill="#e6f51c"/><path d="M13 24V36M27 24V36M20 18V36" stroke="#e6f51c" stroke-width="2"/></svg></div><h3>VERANSTALTUNGEN</h3><p>Lorem ipsum dolor sit amet, consetetur sadipscing elitr, sed diam nonumy eirmod tempor invidunt ut labore et dolore magna aliquyam erat, sed diam voluptua</p></div>
  <div class="abs card" style="left:851px"><div class="ico"><svg width="40" height="40" viewBox="0 0 40 40"><rect x="5" y="16" width="22" height="16" rx="2" fill="#e6f51c"/><path d="M27 21L36 16V32L27 27Z" fill="#e6f51c"/><circle cx="11" cy="10" r="5" fill="#e6f51c"/><circle cx="22" cy="10" r="5" fill="#e6f51c"/></svg></div><h3>FILMPRODUKTIONEN</h3><p>Lorem ipsum dolor sit amet, consetetur sadipscing elitr, sed diam nonumy eirmod tempor invidunt ut labore et dolore magna aliquyam erat, sed diam voluptua</p></div>
</section>

<section>
  <h2 class="abs center h2" style="top:1488px">Einblicke aus unserem<br>Sanitätsdienst</h2>
  <div class="abs rule b" style="top:1574px"></div>
  <div class="abs cols">
    <p>Ganz Ihrem Anlass entsprechend, arbeiten wir in Rettungsdienst-Uniform, legerem Freizeitlook oder in Abendgarderobe. Wir sind, auch wenn man uns nicht sieht, ganz nah dran und können im Fall der Fälle sofort eingreifen. Doch nicht nur unser Erscheinungsbild ist für Ihre Veranstaltung wichtig, sondern vor allem unser Notfall-equipment. So haben wir in unseren Rucksäcken vom Pflaster,</p>
    <p>über Infusionen und Sauerstoff, bis hin zum Defibrillator, alles griffbereit. Auch unsere Rettungswagen sind keine leeren Hüllen sondern allumfänglich ausgestattet. Nur so können wir die ersten entscheidenden Minuten überbrücken, bis der oft-mals überlastete und dadurch verspätet eintreffende öffentliche Rettungsdienst unsere Einsatzstelle erreicht.</p>
  </div>
  <div class="abs slide" role="img" aria-label="Sanitäter in dunkelblauer Uniform versorgen einen älteren Festivalbesucher auf dem Pflaster"></div>
  <div class="abs job">WE <b>♥</b><small>OUR JOB</small></div>
  <svg class="abs arrow" style="top:2127px;left:95px" viewBox="0 0 50 40"><path d="M48 20H8M22 4L6 20L22 36" stroke="#e6f51c" stroke-width="8" fill="none"/></svg>
  <svg class="abs arrow" style="top:2127px;left:1057px" viewBox="0 0 50 40"><path d="M2 20H42M28 4L44 20L28 36" stroke="#e6f51c" stroke-width="8" fill="none"/></svg>
  <div class="abs dots"><i></i><i class="on"></i><i></i><i></i><i></i></div>
</section>

<section>
  <p class="abs center eyebrow" style="top:2515px">Alles für Eure Sicherheit</p>
  <h2 class="abs center h2" style="top:2553px">Partner &amp; Referenzen</h2>
  <div class="abs rule y" style="top:2608px"></div>
  <p class="abs lead" style="top:2650px;left:305px;width:590px">Wir sind stolz darauf, namhafte Kunden wie die "Nordblatt Tageszeitung", das Bundesministerium, den Kesselhaus Club Leipzig, "Wurzelwerk Open Air" und zahlreiche Filmarbeiten zu unseren zufriedenen Kunden zählen zu dürfen. Wir sind bekannt für unsere professionelle Arbeitsweise und die zuverlässige Betreuung bei Veranstaltungen in medizinischen Notfällen (keine ehrenamtlichen „Ersthelfer“!).</p>
  <svg class="abs" style="top:2814px;left:118px" width="50" height="40" viewBox="0 0 50 40"><path d="M48 20H10M24 4L7 20L24 36" stroke="#1b3a8c" stroke-width="8" fill="none"/></svg>
  <svg class="abs" style="top:2814px;left:1032px" width="50" height="40" viewBox="0 0 50 40"><path d="M2 20H40M26 4L43 20L26 36" stroke="#1b3a8c" stroke-width="8" fill="none"/></svg>
  <p class="abs partner" style="top:2796px;left:265px">Nordblatt Tageszeitung</p>
  <p class="abs partner" style="top:2796px;left:505px">Nordblatt Tageszeitung</p>
  <p class="abs partner" style="top:2796px;left:745px">Nordblatt Tageszeitung</p>
  <p class="abs partner" style="top:2858px;left:265px">Nordblatt Tageszeitung</p>
  <p class="abs partner" style="top:2858px;left:505px">Nordblatt Tageszeitung</p>
  <p class="abs partner" style="top:2858px;left:745px">Nordblatt Tageszeitung</p>
</section>

<section>
  <div class="abs staff-bg"></div>
  <div class="abs staff-photo" role="img" aria-label="Team in dunkelblauen Uniformen vor einem Zielbogen bei einem Hindernislauf"></div>
  <h2 class="abs staff-title">Medizinisches Personal für<br>jede Art von Event</h2>
  <div class="abs" style="top:3164px;left:661px;width:100px;height:4px;background:var(--yellow)"></div>
  <p class="abs staff-text">Wenn du eine größere private Feier oder Veranstaltung planst, bei der viele Menschen zusammenkommen, ist es unerlässlich, an die Bereitstellung von medizinischem Personal zu denken. Dabei können Sanitäter, Rettungssanitäter und sogar ein Notarzt von unschätzbarem Wert sein, um die Sicherheit und das Wohlergehen deiner Gäste zu gewährleisten. Unser erfahrenes Team verfügt über umfangreiche Expertise in der medizinischen Betreuung bei Veranstaltungen. Wir können sicherstellen, dass qualifiziertes medizinisches Personal vor Ort ist, um im Falle von Verletzungen, medizinischen Notfällen oder anderen gesundheitlichen Problemen sofortige Hilfe zu leisten.</p>
  <div class="abs acc" style="top:3459px;height:45px">Rettungssanitäter'in<span class="sign">+</span></div>
  <div class="abs acc" style="top:3517px;height:111px">Sanitäter'in<span class="sign">–</span><div class="bar"></div><p>Lorem ipsum dolor sit amet, consetetur sadipscing elitr, sed diam nonumy eirmod tempor invidunt ut labore et dolore magna aliquyam erat, sed diam voluptua</p></div>
  <div class="abs acc" style="top:3643px;height:45px">Notarzt/-ärztin<span class="sign">+</span></div>
</section>

<section class="abs jobs">
  <p class="eyebrow" style="position:absolute;top:80px;width:100%">Lust auf eine neue Herausforderung?</p>
  <h2 class="h2" style="position:absolute;top:118px;width:100%">Wir suchen Dich!</h2>
  <div style="position:absolute;top:174px;left:313px;width:100px;height:4px;background:var(--navy)"></div>
  <p class="lead" style="position:absolute;top:215px;left:80px;width:566px">Wenn Du im medizinischen Personal arbeiten möchtest, dann kontaktiere uns gerne direkt. Wir sind immer auf der Suche nach zuverlässigem medizinischem Personal für unsere Veranstaltungen, Festivals und Clubs.</p>
  <div class="btn">Jetzt bewerben</div>
</section>
</body>
</html>
```